Simple landing page for Brambles cookbook

I need a one page landingpage where customers can order the cookbook.
This is a cookbook of a collection of recipes from our deli that we used to run.
I need a landing page where customers can come and order the book. I also need it coded. I already have the domain through hostwell.
I can send the file of the book through wetransfer. It's too big to upload here. Just so you get the feel that I am looking for.
I attached a simple text as an introduction to the page. But I am open to any suggestions. I want it all to be about the experience that we are sharing the recipes with everybody and that it's for sale. The book is $29.99, shipping included.
Customers have to be able to click and buy the book from it.

Coding

Coded - Design and coding required

Number of Pages Required

1 page

Font styles to use
Sans Serif

Requirements
Must have
• Same colors as the cookbook

```html
<!DOCTYPE html>
<html lang="en">
<head>
<meta charset="utf-8">
<title>Brambles Cookbook</title>
<link href="https://fonts.googleapis.com/css2?family=Playfair+Display:wght@800;900&family=Montserrat:wght@400;800&family=IBM+Plex+Sans:wght@400;500&display=swap" rel="stylesheet">
<style>
  :root {
    --cream: #f4efe3;
    --crimson: #d40a52;
    --brown: #3b2616;
    --ink: #1f1a16;
    --white: #ffffff;
  }
  * { margin: 0; padding: 0; box-sizing: border-box; }
  html, body { width: 1072px; height: 1200px; overflow: hidden; background: var(--white); }
  .page { position: relative; width: 1072px; height: 1200px; font-family: "IBM Plex Sans", sans-serif; color: var(--ink); }

  .hero { position: absolute; left: 0; top: 0; width: 1072px; height: 608px; background: var(--cream); }
  .hero-title { position: absolute; left: 0; width: 734px; top: 138px; text-align: center; font-family: "Playfair Display", serif; font-weight: 900; font-size: 44px; color: var(--brown); line-height: 1.2; }
  .hero-tagline { position: absolute; left: 0; width: 734px; top: 208px; text-align: center; font-family: "Montserrat", sans-serif; font-size: 21px; letter-spacing: 0.8px; line-height: 35px; color: var(--ink); }
  .hero-price { position: absolute; left: 0; width: 730px; top: 288px; text-align: center; font-family: "Playfair Display", serif; font-weight: 900; font-size: 66px; color: var(--crimson); line-height: 1.2; }
  .shipping-badge { position: absolute; left: 261px; top: 386px; width: 202px; height: 37px; border: 1px solid var(--crimson); border-radius: 2px; display: flex; align-items: center; justify-content: center; gap: 8px; font-family: "IBM Plex Sans", sans-serif; font-size: 13.5px; letter-spacing: 0.6px; color: var(--crimson); }
  .buy-button { position: absolute; left: 262px; top: 444px; width: 202px; height: 48px; background: var(--crimson); border-radius: 2px; display: flex; align-items: center; justify-content: center; font-family: "Montserrat", sans-serif; font-weight: 800; font-size: 19px; letter-spacing: 0.5px; color: var(--white); text-decoration: none; }
  .book-cover { position: absolute; left: 647px; top: 64px; width: 266px; height: 472px; background: linear-gradient(170deg, #d9ecf6 0%, #b9d6e8 40%, #c98a45 62%, #e7e4e0 100%); box-shadow: 14px 18px 30px rgba(59,38,22,0.18); }

  .intro { position: absolute; left: 0; top: 608px; width: 1072px; height: 530px; }
  .intro-label { position: absolute; left: 117px; top: 47px; height: 24px; padding: 0 10px; background: var(--crimson); color: var(--white); border-radius: 12px; font-size: 13.5px; font-weight: 500; letter-spacing: 0.3px; line-height: 24px; }
  .intro-title { position: absolute; left: 119px; top: 80px; font-family: "Playfair Display", serif; font-weight: 900; font-size: 40px; color: var(--brown); line-height: 1.2; }
  .intro-photo { position: absolute; left: 114px; top: 150px; width: 351px; height: 342px; border-radius: 4px; background: radial-gradient(ellipse at 50% 50%, #d9b07a 0%, #9fc25a 35%, #e7c98f 60%, #ffffff 82%); }
  .intro-text { position: absolute; left: 511px; top: 68px; width: 441px; font-size: 13.6px; line-height: 18px; text-align: justify; }
  .intro-text p { margin-bottom: 18px; }
  .intro-text .lead { text-align: left; color: #000; }

  .footer { position: absolute; left: 0; top: 1138px; width: 1072px; height: 62px; background: var(--brown); color: var(--white); }
  .footer-name { position: absolute; left: 117px; top: 15px; font-family: "Playfair Display", serif; font-weight: 800; font-size: 20px; }
  .footer-copy { position: absolute; right: 109px; top: 23px; font-size: 11.5px; }
</style>
</head>
<body>
<div class="page">
  <header class="hero">
    <h1 class="hero-title">Brambles Cookbook</h1>
    <p class="hero-tagline">YOUR ULTIMATE GUIDE TO CREATING<br>YOUR OWN FAVOURITE</p>
    <p class="hero-price">$29.99</p>
    <div class="shipping-badge">
      <svg width="24" height="16" viewBox="0 0 24 16" fill="none" stroke="currentColor" stroke-width="1.4">
        <rect x="1" y="2" width="13" height="10" rx="1"/>
        <path d="M14 5h5l4 4v3h-9z"/>
        <circle cx="5.5" cy="13" r="2" fill="var(--cream)"/>
        <circle cx="18" cy="13" r="2" fill="var(--cream)"/>
      </svg>
      SHIPPING INCLUDED
    </div>
    <a class="buy-button" href="#order">BUY NOW</a>
    <div class="book-cover" role="img" aria-label="Cookbook cover with a sandwich photograph on a plate"></div>
  </header>

  <section class="intro">
    <span class="intro-label">WELCOME TO</span>
    <h2 class="intro-title">Brambles Cookbook</h2>
    <div class="intro-photo" role="img" aria-label="Photograph of a tall stacked sandwich with lettuce, cheese, tomato and bacon"></div>
    <div class="intro-text">
      <p class="lead">Opening it’s doors in January of 2010, Brambles European Deli was a sandwich shop in Alderbrook, New Hollis, but also a lot more than that.</p>
      <p>We spent five years with this business until it’s eventual closure in April of 2015. It was a special time where we met tons of amazing people, who we loved to see and serve.</p>
      <p>Brambles started out as a deli but eventually morphed into the sandwich shop we all know it as today.</p>
      <p>We are overwhelmed with the continuous positive messages and commentswe get on our Chatterbox page that is still up and running.</p>
      <p>Unfortunately, we can’t open another Brambles, but we can offer you this collection of our recipes for you to try out at home with your family and friends.</p>
      <p>We truly hope you will enjoy making these sandwiches just as much as we did.</p>
      <p>If you do, please post your pictures of you making a meal or the finished product, or even enjoying it!</p>
    </div>
  </section>

  <footer class="footer">
    <span class="footer-name">Brambles Cookbook</span>
    <span class="footer-copy">Copyright © 2022 All Rights Reserved</span>
  </footer>
</div>
</body>
</html>
```